Design for Chatterly Ad to promote Laptops purchase

Need a graphic design for a Chatterly Ad - to promote 2 laptops (PC and Lumetra) with the stated required ad-text.

AD TEXT:

FOR SME BUSINESS ONLY!
Chat with us!
To get advice on how to apply
and defray up to 80%* of business laptop purchase cost!

*Terms and Conditions apply

Image for reference only

Target Market(s)

Small medium business

Font styles to use
Sans Serif

Requirements
Must have
• 2 laptop images (see attached ) - 1 vector image of LUMETRA , and pls try to create another vector image of PC laptop (where screen is showing Blue Petalix screen)

```html
<!DOCTYPE html>
<html lang="en">
<head>
<meta charset="utf-8">
<title>Chatterly Ad – SME Business Laptops</title>
<link href="https://fonts.googleapis.com/css2?family=Mukta:wght@400;600;700&display=swap" rel="stylesheet">
<style>
  :root {
    --backdrop: #6b6b6b;
    --light-bg: #ffffff;
    --dark-bg: #333333;
    --ink-dark: #111111;
    --ink-light: #ffffff;
    --lumetra-screen-a: #f3a6f0;
    --lumetra-screen-b: #7b3fc0;
    --lumetra-body: #c9c9cc;
    --petalix-screen-a: #3aa0f0;
    --petalix-screen-b: #0b2c6e;
    --petalix-body: #b9c0c8;
  }
  * { margin: 0; padding: 0; box-sizing: border-box; }
  html, body { width: 982px; height: 1200px; overflow: hidden; }
  body {
    background: var(--backdrop);
    font-family: "Mukta", "Segoe UI", sans-serif;
    position: relative;
  }
  .ad-banner {
    position: absolute;
    left: 87px;
    width: 808px;
    height: 422px;
    text-align: center;
  }
  .ad-banner--light { top: 112px; background: var(--light-bg); color: var(--ink-dark); }
  .ad-banner--dark { top: 677px; background: var(--dark-bg); color: var(--ink-light); }

  .laptop-art { position: absolute; }
  .laptop-art--lumetra {
    left: 63px; top: 35px; width: 330px; height: 167px;
    background: linear-gradient(160deg, var(--lumetra-screen-a) 0%, var(--lumetra-screen-b) 55%, var(--lumetra-body) 100%);
    border-radius: 10px 10px 4px 4px;
  }
  .laptop-art--petalix {
    left: 483px; top: 35px; width: 246px; height: 184px;
    background: linear-gradient(170deg, var(--petalix-screen-b) 0%, var(--petalix-screen-a) 45%, var(--petalix-body) 75%);
    border-radius: 6px;
  }

  .headline {
    position: absolute; left: 0; right: 0; top: 218px;
    font-size: 48px; font-weight: 600; line-height: 1; letter-spacing: 0.5px;
  }
  .chat-cta {
    position: absolute; left: 0; right: 0; top: 279px;
    font-size: 24px; font-weight: 400; line-height: 1;
  }
  .chat-cta strong, .offer strong { font-weight: 700; }
  .offer {
    position: absolute; left: 0; right: 0; top: 314px;
    font-size: 20px; line-height: 28px;
  }
  .terms {
    position: absolute; left: 62px; top: 379px;
    font-size: 13px; line-height: 1; text-align: left;
  }
</style>
</head>
<body>

<section class="ad-banner ad-banner--light">
  <div class="laptop-art laptop-art--lumetra" role="img" aria-label="Lumetra laptop with a pink and purple glowing screen"></div>
  <div class="laptop-art laptop-art--petalix" role="img" aria-label="Silver PC laptop showing a blue Petalix start screen"></div>
  <h1 class="headline">SME BUSINESS ONLY!</h1>
  <p class="chat-cta"><strong>Chat</strong> with us!</p>
  <p class="offer">To get advice on how to apply<br>and defray <strong>up to 80%*</strong> of business laptop purchase cost!</p>
  <p class="terms">*Terms and Conditions apply</p>
</section>

<section class="ad-banner ad-banner--dark">
  <div class="laptop-art laptop-art--lumetra" role="img" aria-label="Lumetra laptop with a pink and purple glowing screen"></div>
  <div class="laptop-art laptop-art--petalix" role="img" aria-label="Silver PC laptop showing a blue Petalix start screen"></div>
  <h2 class="headline">SME BUSINESS ONLY!</h2>
  <p class="chat-cta"><strong>Chat</strong> with us!</p>
  <p class="offer">To get advice on how to apply<br>and defray <strong>up to 80%*</strong> of business laptop purchase cost!</p>
  <p class="terms">*Terms and Conditions apply</p>
</section>

</body>
</html>
```